Consulting company requires a logo and business card design

I require a logo/business card design for a new company based in Sexsmith Alberta called TallMarsh Integrity Consulting Ltd. I plan to provide the following services: Construction management/inspection for the oil and gas industry, as well as general consulting for Asset Management, fleet management, etc. Have attached a copy of resume for use as guide for

Target Market(s)

Businesses within the oil and gas production, construction and shipping industry

Industry/Entity Type

Oil And Gas

Contact Information for Business Card

Believe should highlight, services offered, safety, quality,

Logo Text

TallMarsh Integrity Consulting (TMIC) ?

Font styles to use
Script

Requirements
Must have
• Open to all options

```html
<!DOCTYPE html>
<html lang="en">
<head>
<meta charset="utf-8">
<title>TallMarsh Integrity Consulting Ltd. – Business Card</title>
<link rel="stylesheet" href="https://fonts.googleapis.com/css2?family=Open+Sans:wght@400;600&display=swap">
<style>
  :root {
    --backdrop: #2b2522;
    --card-front: #1c1c1e;
    --card-back-top: #5b86cf;
    --card-back-bottom: #7fd3e6;
    --accent-blue: #6cb8ea;
    --text-light: #e4e4e4;
    --text-muted: #bdbdbd;
    --divider: #3a3a3d;
    --mark-circle: #5aa6de;
  }
  * { margin: 0; padding: 0; box-sizing: border-box; }
  html, body {
    width: 1200px; height: 844px; overflow: hidden;
    background: var(--backdrop);
    font-family: "Open Sans", Arial, sans-serif;
  }
  .canvas { position: relative; width: 1200px; height: 844px; }

  .card {
    position: absolute; top: 262px;
    width: 560px; height: 320px;
    border-radius: 3px;
    box-shadow: 0 14px 30px rgba(0,0,0,0.45);
    overflow: hidden;
  }
  .card--front { left: 30px; background: var(--card-front); }
  .card--back {
    left: 610px;
    background: linear-gradient(160deg, var(--card-back-top) 0%, var(--card-back-bottom) 100%);
    display: flex; flex-direction: column; align-items: center; justify-content: center; gap: 18px;
  }

  .brand {
    position: absolute; left: 0; top: 0; width: 290px; height: 320px;
    display: flex; flex-direction: column; align-items: center; justify-content: center; gap: 14px;
    text-align: center;
  }
  .brand__mark {
    width: 30px; height: 30px; border-radius: 50%;
    background: var(--mark-circle);
  }
  .brand__name {
    color: var(--accent-blue);
    font-size: 21px; font-weight: 400; line-height: 1.3;
    letter-spacing: 0.5px;
  }

  .divider {
    position: absolute; left: 296px; top: 90px;
    width: 1px; height: 170px; background: var(--divider);
  }

  .contact {
    position: absolute; left: 318px; top: 92px;
    color: var(--text-light); font-size: 13px; line-height: 1.4;
  }
  .contact__name { color: var(--accent-blue); font-size: 16px; font-weight: 600; }
  .contact__role { margin-bottom: 14px; }
  .contact__address { margin-bottom: 14px; }
  .contact__line { display: flex; align-items: center; gap: 8px; }
  .contact__line svg { width: 11px; height: 11px; fill: none; stroke: var(--accent-blue); stroke-width: 1.6; }

  .back__mark {
    width: 64px; height: 64px; border-radius: 50%;
    background: rgba(255,255,255,0.25);
  }
  .back__name { color: #ffffff; font-size: 22px; font-weight: 400; letter-spacing: 0.5px; }
</style>
</head>
<body>
<main class="canvas">
  <section class="card card--front" aria-label="Business card front">
    <div class="brand">
      <span class="brand__mark" aria-hidden="true"></span>
      <div class="brand__name">TallMarsh<br>Integrity Consulting Ltd.</div>
    </div>
    <div class="divider"></div>
    <div class="contact">
      <div class="contact__name">Daniel Reeve</div>
      <div class="contact__role">Managing Director</div>
      <div class="contact__address">12345, Address Goes Here<br>Country Name, 123456.</div>
      <div class="contact__line">
        <svg viewBox="0 0 12 12"><path d="M2 1.5h2.5l1 2.5-1.5 1a6 6 0 0 0 3 3l1-1.5 2.5 1v2.5A8.5 8.5 0 0 1 2 1.5z"/></svg>
        044-555 210 387
      </div>
      <div class="contact__line">
        <svg viewBox="0 0 12 12"><rect x="1" y="2.5" width="10" height="7"/><path d="M1 2.5l5 4 5-4"/></svg>
        info@tallmarshic.com
      </div>
      <div class="contact__line">
        <svg viewBox="0 0 12 12"><path d="M5 7l2-2M4.5 5.5l-2 2a1.6 1.6 0 0 0 2 2l2-2M7.5 6.5l2-2a1.6 1.6 0 0 0-2-2l-2 2"/></svg>
        www.tallmarshic.com
      </div>
    </div>
  </section>

  <section class="card card--back" aria-label="Business card back">
    <span class="back__mark" aria-hidden="true"></span>
    <div class="back__name">TallMarsh Integrity Consulting Ltd.</div>
  </section>
</main>
</body>
</html>
```